Business Card Design (NEW FILES)

ATTENTION: New vector files are available. Please update your design to reflect/use the new (better resolution) logo images.

Seeking a unique and professional business card design for a commercial drone photography/videography business. The layout should feature
the logo (attached) and include the following information:
Owen Tarrick
614-502-7738
www.skylarkreelworks.example
NRD Certified Remote Pilot

Owen Tarrick

```html
<!DOCTYPE html>
<html lang="en">
<head>
<meta charset="utf-8">
<title>Skylark Reelworks – Business Card</title>
<link rel="stylesheet" href="https://fonts.googleapis.com/css2?family=Open+Sans:wght@400;600;700&display=swap">
<style>
  :root {
    --stage: #232323;
    --navy: #12174a;
    --orange: #e4864f;
    --orange-deep: #c96e3b;
    --white: #ffffff;
    --mist: #dfe3ee;
  }
  * { box-sizing: border-box; margin: 0; padding: 0; }
  html, body { width: 1200px; height: 780px; overflow: hidden; background: var(--stage); }
  body { font-family: "Open Sans", Arial, sans-serif; }
  .stage { position: relative; width: 1200px; height: 780px; display: flex; align-items: center; justify-content: center; gap: 40px; }

  .card { position: relative; width: 540px; height: 308px; border-radius: 22px; overflow: hidden; box-shadow: 0 18px 40px rgba(0,0,0,.45); }

  /* Front */
  .card-front { background: var(--navy); color: var(--white); }
  .brand { position: absolute; left: 34px; top: 36px; display: flex; align-items: center; gap: 10px; }
  .brand-name { font-size: 25px; font-weight: 600; letter-spacing: 1.5px; text-transform: uppercase; line-height: 1.15; color: var(--white); }
  .brand-dot { width: 18px; height: 18px; border-radius: 50%; background: var(--orange); flex: none; }
  .divider { position: absolute; left: 0; top: 0; width: 540px; height: 308px; pointer-events: none; }

  .person { position: absolute; left: 292px; top: 98px; }
  .person-name { font-size: 30px; font-weight: 700; line-height: 1; white-space: nowrap; }
  .person-name .first { color: var(--orange); }
  .person-role { font-size: 13px; margin-top: 4px; }
  .contacts { list-style: none; margin-top: 12px; }
  .contacts li { display: flex; align-items: center; gap: 8px; font-size: 12.5px; line-height: 1.75; white-space: nowrap; }
  .contacts svg { width: 12px; height: 12px; flex: none; }

  .credential-band { position: absolute; left: 0; bottom: 0; width: 420px; height: 38px; background: var(--orange); display: flex; align-items: center; padding-left: 24px; font-size: 14px; font-weight: 600; color: var(--white); }
  .drone-art { position: absolute; right: 0; bottom: 0; width: 140px; height: 66px; background: linear-gradient(135deg, var(--orange) 0%, var(--white) 45%, var(--mist) 100%); clip-path: polygon(0 42%, 30% 0, 100% 0, 100% 100%, 0 100%); }

  /* Back */
  .card-back { background: var(--orange); display: flex; align-items: center; justify-content: center; }
  .back-brand { display: flex; align-items: center; gap: 14px; }
  .back-brand .brand-name { font-size: 38px; color: var(--orange-deep); }
  .back-brand .brand-dot { width: 26px; height: 26px; background: var(--orange-deep); }
</style>
</head>
<body>
<main class="stage">
  <section class="card card-front" aria-label="Card front">
    <div class="brand">
      <span class="brand-name">Skylark<br>Reelworks</span>
      <span class="brand-dot"></span>
    </div>

    <svg class="divider" viewBox="0 0 540 308" aria-hidden="true">
      <line x1="280" y1="96" x2="206" y2="228" stroke="var(--orange)" stroke-width="1"/>
    </svg>

    <div class="person">
      <p class="person-name"><span class="first">Owen</span> Tarrick</p>
      <p class="person-role">Owner</p>
      <ul class="contacts">
        <li>
          <svg viewBox="0 0 24 24" aria-hidden="true"><path fill="var(--orange)" d="M6.6 10.8a15.1 15.1 0 006.6 6.6l2.2-2.2c.3-.3.7-.4 1-.2 1.1.4 2.3.6 3.6.6.6 0 1 .4 1 1V20c0 .6-.4 1-1 1C10.6 21 3 13.4 3 4c0-.6.4-1 1-1h3.5c.6 0 1 .4 1 1 0 1.3.2 2.5.6 3.6.1.3 0 .7-.2 1z"/></svg>
          614-502-7738
        </li>
        <li>
          <svg viewBox="0 0 24 24" aria-hidden="true"><circle cx="12" cy="12" r="9" fill="none" stroke="var(--orange)" stroke-width="2.4"/><path d="M3 12h18M12 3c3 3 3 15 0 18M12 3c-3 3-3 15 0 18" fill="none" stroke="var(--orange)" stroke-width="1.6"/></svg>
          www.skylarkreelworks.example
        </li>
        <li>
          <svg viewBox="0 0 24 24" aria-hidden="true"><rect x="2" y="5" width="20" height="14" rx="2" fill="var(--orange)"/><path d="M3 6l9 7 9-7" fill="none" stroke="var(--navy)" stroke-width="1.8"/></svg>
          info@skylarkreelworks.example
        </li>
      </ul>
    </div>

    <div class="credential-band">NRD Certified Remote Pilot, Fully Insured</div>
    <div class="drone-art" role="img" aria-label="Illustration of a camera drone in flight"></div>
  </section>

  <section class="card card-back" aria-label="Card back">
    <div class="back-brand">
      <span class="brand-name">Skylark<br>Reelworks</span>
      <span class="brand-dot"></span>
    </div>
  </section>
</main>
</body>
</html>
```